International Medical Company Needs a Website Design for a Support Site

We need a website design for a support site we are doing for ostomates called Bright Returns. We are an international company but this website is for our Australian market.

The website is a support site for people who are living with an Ostomy or Bowel Disease. This is a site where they can read other ostomates' stories and how they are dealing with the fact that they have to wear a pouch everyday.

The URL for our US site is: http://www.brightreturnsite.example/

We need to use the same logo but we have freedom around the color scheme. We are not fond of the brown color scheme used in our US site and are happy for designs to be submitted with alternatives.

• We want the design to be clean, inspiring, modern and inviting.
• We would like to see a design for the mainpage / homepage and one of the subpages
• We only require the PSD / image files (no HTML needed)

Attached to this project is our sitemap, an example wireframe and the logos. We are happy for you to play around with different options and don't have to stick to the layout shown in the wireframe.

If you have any further questions please ask.

Industry/Entity Type

It Company

```html
<!DOCTYPE html>
<html lang="en">
<head>
<meta charset="utf-8">
<title>Bright Returns – Sharing Stories &amp; Giving Hope</title>
<link rel="stylesheet" href="https://fonts.googleapis.com/css2?family=Amatic+SC:wght@700&family=Roboto:wght@400;500;700&display=swap">
<style>
:root{
  --brand:#1f7a80;
  --brand-dark:#175f64;
  --heading:#1f7a80;
  --charcoal:#2f3a3d;
  --nav:#2f3a3d;
  --nav-line:#425054;
  --text:#5a5a5a;
  --title:#222;
  --accent:#e0561f;
  --footer:#1b2326;
  --page:#f4f6f6;
  --quote:#241a10;
}
*{box-sizing:border-box;margin:0;padding:0}
html,body{width:1200px;height:928px;overflow:hidden}
body{font-family:"Roboto",Arial,sans-serif;background:var(--page);position:relative;color:var(--text)}
a{text-decoration:none;color:inherit}
.top-rule{position:absolute;left:0;top:0;width:1200px;height:6px;background:var(--brand)}
.brand{position:absolute;left:200px;top:20px;width:130px;height:88px;display:flex;flex-direction:column;align-items:flex-start;justify-content:flex-end}
.brand-mark{width:22px;height:22px;border-radius:50%;background:var(--brand);margin:0 0 12px 48px}
.brand-name{font-size:15px;font-weight:500;letter-spacing:1px;color:var(--brand);text-transform:uppercase;white-space:nowrap}
.util-share{position:absolute;left:822px;top:26px;width:107px;height:24px;border:1px solid #cfcfcf;background:linear-gradient(#fff,#ececec);font-size:10px;color:#222;display:flex;align-items:center;justify-content:center}
.lang{position:absolute;left:944px;top:26px;width:54px;height:24px;border:1px solid #cfcfcf;background:linear-gradient(#fff,#ececec);display:flex}
.lang .flag{width:16px;height:11px;margin:6px 0 0 9px;background:linear-gradient(#b22 0 50%,#fff 50% 60%,#b22 60%);position:relative}
.lang .flag::before{content:"";position:absolute;left:0;top:0;width:7px;height:6px;background:#2a3e7a}
.lang .caret{margin-left:auto;width:20px;border-left:1px solid #d6d6d6;display:flex;align-items:center;justify-content:center}
.main-nav{position:absolute;left:374px;top:70px;width:625px;height:41px;background:var(--nav);border-radius:5px;display:flex;overflow:hidden}
.main-nav a{color:#fff;font-size:10.5px;display:flex;align-items:center;justify-content:center;height:100%;border-right:1px solid var(--nav-line)}
.main-nav a:last-child{border-right:0}
.main-nav a.active{background:var(--brand)}
.hero{position:absolute;left:200px;top:126px;width:800px;height:294px;display:flex}
.hero-intro{width:279px;background:var(--charcoal);padding:34px 20px 0 20px;color:#fff}
.hero-intro h1{font-size:15.5px;font-weight:400;margin-bottom:14px}
.hero-intro p{font-size:11.5px;line-height:19px}
.btn{display:flex;align-items:center;justify-content:center;width:249px;height:30px;background:linear-gradient(#fff,#e4e4e4);border:1px solid #ccc;color:#222;font-size:12px}
.btn.first{margin-top:28px}
.or{font-size:9.5px;text-align:center;margin:12px 0;color:#ddd;width:249px;display:block}
.hero-slide{flex:1;position:relative;background:linear-gradient(180deg,#9a6a2a 0%,#e9a43e 35%,#f3c16a 60%,#c77a22 82%,#1b140c 100%)}
.slide-quote{position:absolute;left:145px;top:68px;width:370px;font-family:"Amatic SC",cursive;font-weight:700;font-size:37px;line-height:40px;color:var(--quote)}
.arrow{position:absolute;top:119px;width:28px;height:28px;border-radius:50%;background:rgba(255,255,255,.55);display:flex;align-items:center;justify-content:center}
.arrow.prev{left:27px}.arrow.next{right:27px}
.dots{position:absolute;left:290px;top:264px;display:flex;gap:7px}
.dots span{width:10px;height:10px;border-radius:50%;border:1.5px solid #fff}
.dots span.on{background:#fff;border-color:#777;opacity:.6}
.col{position:absolute;top:450px}
.col h2{font-size:20.5px;font-weight:400;color:var(--heading);height:36px}
.feature{width:254px}
.feature .photo{width:254px;height:171px;border:1px solid #ddd}
.feature h3{font-size:12px;font-weight:400;color:var(--title);margin-top:11px}
.feature p{font-size:10px;line-height:19.2px;margin-top:3px}
.more{display:block;font-size:10px;color:var(--accent);margin-top:6px}
.news{left:738px;width:262px}
.news-item{display:flex;height:78px}
.news-item .thumb{width:75px;height:70px;flex:none;border:1px solid #ddd}
.news-item .body{margin-left:13px;margin-top:3px}
.news-item h4{font-size:11px;font-weight:500;color:#555;letter-spacing:.2px}
.news-item p{font-size:9.5px;line-height:11px;margin-top:6px;width:160px}
.news-item .more{font-weight:500;margin-top:6px}
.footer{position:absolute;left:0;top:822px;width:1200px;height:106px;background:var(--footer);border-top:6px solid var(--brand)}
.footer-links{position:absolute;left:200px;top:30px;font-size:10px;font-weight:500;color:#fff}
.copyright{position:absolute;left:200px;top:58px;font-size:10px;font-weight:500;color:#fff}
.social{position:absolute;left:894px;top:26px;display:flex;gap:4px}
.social span{width:18px;height:18px;border-radius:2px}
</style>
</head>
<body>
<div class="top-rule"></div>

<header>
  <a class="brand" href="http://www.brightreturnsite.example/">
    <span class="brand-mark"></span>
    <span class="brand-name">Bright Returns</span>
  </a>
  <div class="util-share">Share A Story</div>
  <div class="lang"><span class="flag"></span><span class="caret"><svg width="6" height="4"><path d="M0 0h6L3 4z" fill="#777"/></svg></span></div>
  <nav class="main-nav">
    <a class="active" style="width:87px">About Us</a>
    <a style="width:113px">Personal Stories</a>
    <a style="width:100px">Tips For Living</a>
    <a style="width:68px">News</a>
    <a style="width:103px">Resources</a>
    <a style="width:86px">Contact Us</a>
    <a style="width:68px">Search</a>
  </nav>
</header>

<section class="hero">
  <div class="hero-intro">
    <h1>Sharing Stories &amp; Giving Hope</h1>
    <p>to people around the world who are facing inflammatory bowel disease, colorectal cancer, or have had ostomy surgery</p>
    <a class="btn first">Share A Story</a>
    <span class="or">Or</span>
    <a class="btn">Read Stories</a>
  </div>
  <div class="hero-slide" role="img" aria-label="Sunset over tall grass with a palm tree silhouette">
    <p class="slide-quote">We all live under the same sky, but we don't all have the same horizon. ~Karl Aldinger</p>
    <span class="arrow prev"><svg width="10" height="14"><path d="M8 1L2 7l6 6" stroke="#888" stroke-width="2.5" fill="none"/></svg></span>
    <span class="arrow next"><svg width="10" height="14"><path d="M2 1l6 6-6 6" stroke="#888" stroke-width="2.5" fill="none"/></svg></span>
    <div class="dots"><span class="on"></span><span></span><span></span></div>
  </div>
</section>

<section class="col feature" style="left:199px">
  <h2>What is Bright Returns</h2>
  <div class="photo" role="img" aria-label="Business handshake in a bright office" style="background:linear-gradient(135deg,#c9d8e6,#e6c9b2 55%,#9fb5c9)"></div>
  <h3>City landscape photography</h3>
  <p>Quisque pellentesque fringilla scelerisque. Donec porta urna eu fringilla adipiscing. Nullam id eleifend massa. Curabitur eu blandit sapien. In et nibh ornare, blandit mi vel, imperdiet dui. Aenean ante libero,...</p>
  <a class="more">Read more</a>
</section>

<section class="col feature" style="left:470px">
  <h2>Share A Story</h2>
  <div class="photo" role="img" aria-label="Hands using a tablet showing charts beside a coffee cup" style="background:linear-gradient(135deg,#8a8f96,#d9dde2 50%,#b7bcc2)"></div>
  <h3>City landscape photography</h3>
  <p>Quisque pellentesque fringilla scelerisque. Donec porta urna eu fringilla adipiscing. Nullam id eleifend massa. Curabitur eu blandit sapien. In et nibh ornare, blandit mi vel, imperdiet dui. Aenean ante libero,...</p>
  <a class="more">Read more</a>
</section>

<section class="col news">
  <h2>News</h2>
  <div class="news-item">
    <div class="thumb" role="img" aria-label="Quote card on teal" style="background:#2fb3c6"></div>
    <div class="body"><h4>SUSPENDISSE MATTIS TELI</h4><p>Suspendisse mattis tellus vel augue mollis ultrices suspends</p><a class="more">Read More +</a></div>
  </div>
  <div class="news-item">
    <div class="thumb" role="img" aria-label="Quote card on blue" style="background:#39b4e2"></div>
    <div class="body"><h4>SUSPENDISSE MATTIS TELI</h4><p>Suspendisse mattis tellus vel augue mollis ultrices suspends</p><a class="more">Read More +</a></div>
  </div>
  <div class="news-item">
    <div class="thumb" role="img" aria-label="Quote card on dark green" style="background:#3f5a46"></div>
    <div class="body"><h4>SUSPENDISSE MATTIS TELI</h4><p>Suspendisse mattis tellus vel augue mollis ultrices suspends</p><a class="more">Read More +</a></div>
  </div>
  <div class="news-item">
    <div class="thumb" role="img" aria-label="Quote card on tan" style="background:#c8a07a"></div>
    <div class="body"><h4>SUSPENDISSE MATTIS TELI</h4><p>Suspendisse mattis tellus vel augue mollis ultrices suspends</p><a class="more">Read More +</a></div>
  </div>
</section>

<footer class="footer">
  <div class="footer-links">Legal Notice \&nbsp; Privacy Policy \ Sitemap</div>
  <div class="copyright">Copyright © 2014 Bright Returns All Rights Reserved</div>
  <div class="social">
    <span style="background:#3b5a9a"></span>
    <span style="background:#3aa6dc"></span>
    <span style="background:#d14836"></span>
    <span style="background:#c9283e"></span>
    <span style="background:#f2f2f2"></span>
  </div>
</footer>
</body>
</html>
```